Business card design needed

Card needs to say

Maren Heathwold
Investor - Solutions - Development

My business is in property deals. I would like the words above to be on the card. I have attached a logo for you to copy/recreate.
On the back you could list the following:

Creative property solutions

Thankyou, Maren

Target Market(s)

people wanting to get into the property market, desperate sellers, Mums & Dads wanting to help their kids to purchase a property. People who want to create wealth. People who are stuck and need a solution.

Industry/Entity Type

Business

Contact Information for Business Card

T: 0431 274 506
F: (07) 3842 1739
E: maren47@vbx-mail.com.au

Requirements
Must have
• Simple and effective.
Look like I am here to help
Should not have
• Should not look like a realestate agent

```html
<!DOCTYPE html>
<html lang="en">
<head>
<meta charset="utf-8">
<title>Maren Heathwold – Business Card</title>
<link rel="stylesheet" href="https://fonts.googleapis.com/css2?family=Arimo:wght@400;700&display=swap">
<style>
  :root {
    --backdrop: #1c1c1c;
    --card: #2a2828;
    --green: #7dc142;
    --blue: #2a9fd8;
  }
  * { margin: 0; padding: 0; box-sizing: border-box; }
  html, body {
    width: 1200px;
    height: 900px;
    overflow: hidden;
    background: var(--backdrop);
    font-family: "Arimo", Arial, sans-serif;
  }
  .card {
    position: absolute;
    left: 310px;
    width: 580px;
    height: 331px;
    background: var(--card);
    box-shadow: 0 10px 30px rgba(0,0,0,.6);
  }
  .card--back { top: 80px; }
  .card--front { top: 480px; }

  /* back side */
  .back-content {
    position: absolute;
    right: 48px;
    top: 70px;
    text-align: left;
  }
  .brand-mark {
    display: inline-block;
    width: 14px;
    height: 14px;
    background: var(--green);
    margin-right: 10px;
    vertical-align: middle;
  }
  .back-name {
    color: var(--green);
    font-weight: 700;
    font-size: 30px;
    letter-spacing: .2px;
    line-height: 1;
  }
  .back-tagline {
    color: var(--blue);
    font-weight: 700;
    font-size: 14px;
    margin: 6px 0 0 82px;
  }
  .contact {
    list-style: none;
    margin-top: 38px;
    font-size: 14px;
    line-height: 1.5;
    color: var(--blue);
    text-align: right;
  }
  .contact .label { color: var(--green); }

  /* front side */
  .front-content {
    position: absolute;
    left: 0;
    right: 0;
    top: 118px;
    text-align: center;
  }
  .front-name {
    color: var(--green);
    font-weight: 700;
    font-size: 42px;
    line-height: 1;
  }
  .front-tagline {
    color: var(--blue);
    font-weight: 700;
    font-size: 16px;
    margin-top: 8px;
    letter-spacing: .2px;
  }
</style>
</head>
<body>
  <section class="card card--back" aria-label="Card back">
    <div class="back-content">
      <h2 class="back-name"><span class="brand-mark"></span>Maren Heathwold</h2>
      <p class="back-tagline">Creative property solutions</p>
      <ul class="contact">
        <li><span class="label">T:</span> 0431 274 506 <span class="label">F:</span> (07) 3842 1739</li>
        <li><span class="label">E:</span> maren47@vbx-mail.com.au</li>
      </ul>
    </div>
  </section>

  <section class="card card--front" aria-label="Card front">
    <div class="front-content">
      <h1 class="front-name">Maren Heathwold</h1>
      <p class="front-tagline">Investor - Solutions - Development</p>
    </div>
  </section>
</body>
</html>
```